Stonebridge Building and Projects business cards

A business card with watermark background (construction work)

Company logo attached

Home improvement projects
House renovations
Bathroom and kitchen renovations
House extensions
New builds and granny flats

Director Omar Haddani
(Phone number)
omar@sbpbuilding.com.au
(Instagram logo) sbp_building

```html
<!DOCTYPE html>
<html lang="en">
<head>
<meta charset="utf-8">
<title>Stonebridge Building and Projects – Business Cards</title>
<link rel="stylesheet" href="https://fonts.googleapis.com/css2?family=Montserrat:wght@600;700&family=Arimo:wght@400&display=swap">
<style>
  :root {
    --stage: #e4e4e2;
    --card: #ffffff;
    --card-shade: #f1f1f0;
    --brand-blue: #2c6fb3;
    --ink: #2b2b2b;
    --rule: #3a3a3a;
  }
  * { box-sizing: border-box; margin: 0; padding: 0; }
  html, body {
    width: 1200px; height: 801px; overflow: hidden;
    background: var(--stage);
  }
  .stage {
    width: 1200px; height: 801px;
    display: flex; align-items: center; justify-content: center; gap: 40px;
  }
  .card {
    position: relative;
    width: 540px; height: 310px;
    background: linear-gradient(160deg, var(--card) 0%, var(--card-shade) 100%);
    box-shadow: 0 6px 18px rgba(0,0,0,.14);
    font-family: "Arimo", Arial, sans-serif;
    color: var(--ink);
  }
  .wordmark {
    display: flex; align-items: center; gap: 10px;
    font-family: "Montserrat", Arial, sans-serif;
    font-weight: 700; color: var(--brand-blue);
    line-height: 1.15; font-size: 22px;
  }
  .wordmark-square {
    flex: none; width: 34px; height: 34px; background: var(--brand-blue);
  }
  .tagline {
    margin-top: 8px; padding-top: 6px;
    border-top: 2px solid var(--brand-blue);
    font-size: 13px; color: var(--brand-blue);
  }

  /* Front */
  .card-front .brand { position: absolute; left: 60px; top: 40px; width: 300px; }
  .card-front .person { position: absolute; left: 40px; top: 200px; width: 210px; text-align: right; }
  .person-name {
    font-family: "Montserrat", Arial, sans-serif; font-weight: 700;
    font-size: 22px; color: var(--brand-blue);
  }
  .person-role { font-size: 15px; margin-top: 4px; }
  .card-front .divider {
    position: absolute; left: 268px; top: 186px; width: 1px; height: 86px; background: var(--rule);
  }
  .contacts { position: absolute; left: 286px; top: 190px; list-style: none; }
  .contacts li {
    display: flex; align-items: center; gap: 9px;
    font-size: 14px; height: 26px;
  }
  .contacts svg { flex: none; width: 14px; height: 14px; fill: var(--brand-blue); }
  .icon-dot { width: 12px; height: 12px; border-radius: 50%; background: var(--brand-blue); flex: none; margin: 0 1px; }

  /* Back */
  .card-back .brand { position: absolute; left: 34px; top: 96px; width: 220px; }
  .card-back .wordmark { font-size: 19px; }
  .card-back .divider {
    position: absolute; left: 270px; top: 70px; width: 1px; height: 170px; background: var(--rule);
  }
  .services { position: absolute; left: 290px; top: 78px; list-style: none; }
  .services li {
    display: flex; align-items: center; gap: 8px;
    font-size: 14.5px; height: 31px;
  }
  .services li::before {
    content: ""; width: 6px; height: 6px; border-radius: 50%; background: var(--brand-blue); flex: none;
  }
</style>
</head>
<body>
<main class="stage">

  <section class="card card-front" aria-label="Business card front">
    <div class="brand">
      <div class="wordmark"><span class="wordmark-square"></span><span>Stonebridge Building and Projects</span></div>
      <p class="tagline">Built right, built to last</p>
    </div>
    <div class="person">
      <p class="person-name">Omar Haddani</p>
      <p class="person-role">Director</p>
    </div>
    <span class="divider"></span>
    <ul class="contacts">
      <li>
        <svg viewBox="0 0 24 24" aria-hidden="true"><path d="M6.6 10.8a15.1 15.1 0 0 0 6.6 6.6l2.2-2.2a1 1 0 0 1 1-.25 11.4 11.4 0 0 0 3.6.57 1 1 0 0 1 1 1V20a1 1 0 0 1-1 1A17 17 0 0 1 3 4a1 1 0 0 1 1-1h3.5a1 1 0 0 1 1 1c0 1.25.2 2.45.57 3.57a1 1 0 0 1-.25 1z"/></svg>
        02 5550 1847
      </li>
      <li>
        <svg viewBox="0 0 24 24" aria-hidden="true"><path d="M2 5h20v14H2z" fill="none"/><path d="M2 5h20L12 13z"/><path d="M2 7l10 8 10-8v12H2z"/></svg>
        omar@sbpbuilding.com.au
      </li>
      <li><span class="icon-dot"></span>sbp_building</li>
    </ul>
  </section>

  <section class="card card-back" aria-label="Business card back">
    <div class="brand">
      <div class="wordmark"><span class="wordmark-square"></span><span>Stonebridge Building and Projects</span></div>
      <p class="tagline">Built right, built to last</p>
    </div>
    <span class="divider"></span>
    <ul class="services">
      <li>Home improvement projects</li>
      <li>House renovations</li>
      <li>Bathroom and kitchen renovations</li>
      <li>House extensions</li>
      <li>New builds and granny flats</li>
    </ul>
  </section>

</main>
</body>
</html>
```